Awesome photographers card for an awesome new business

Double sided business card Black background and silver logo in middle on one side. Details on otherside. please keep it simple

Industry/Entity Type

Photographer

Contact Information for Business Card

Gerald Fenwick
0452817360
GeraldFenwickPhotography47@mailbox.test
www.GeraldFenwickPhotography.test.au
Instagram _Gerald_fenwick

Requirements
Must have
• My logo in Silver
• please use instagram logo instead of "Instagram"

```html
<!DOCTYPE html>
<html lang="en">
<head>
<meta charset="utf-8">
<title>Gerald Fenwick Photography – Business Card</title>
<link rel="stylesheet" href="https://fonts.googleapis.com/css2?family=Nunito+Sans:wght@400;600&display=swap">
<style>
  :root {
    --backdrop: #1f1f1f;
    --card-black: #0c0c0c;
    --card-sheen: #1a1a1a;
    --silver: #c9c9c9;
    --text-white: #f2f2f2;
  }
  * { margin: 0; padding: 0; box-sizing: border-box; }
  html, body {
    width: 1200px;
    height: 930px;
    overflow: hidden;
    background: var(--backdrop);
    font-family: "Nunito Sans", sans-serif;
  }
  .card-set {
    position: relative;
    width: 1200px;
    height: 930px;
  }
  .card {
    position: absolute;
    left: 280px;
    width: 640px;
    height: 390px;
    background: linear-gradient(135deg, var(--card-black) 0%, var(--card-sheen) 55%, var(--card-black) 100%);
    box-shadow: 0 12px 30px rgba(0, 0, 0, 0.5);
  }
  .card--front { top: 50px; }
  .card--back { top: 490px; }

  .brand-mark {
    position: absolute;
    top: 50%;
    left: 50%;
    transform: translate(-50%, -50%);
    display: flex;
    align-items: center;
    gap: 14px;
    white-space: nowrap;
  }
  .brand-mark__dot {
    flex: none;
    width: 18px;
    height: 18px;
    border-radius: 50%;
    background: var(--silver);
  }
  .brand-mark__name {
    color: var(--silver);
    font-weight: 600;
    font-size: 26px;
    letter-spacing: 0.18em;
    text-transform: uppercase;
  }

  .holder-name {
    position: absolute;
    top: 128px;
    left: 250px;
    color: var(--text-white);
    font-weight: 600;
    font-size: 15px;
    letter-spacing: 0.3em;
    text-transform: uppercase;
    white-space: nowrap;
  }
  .contact-list {
    position: absolute;
    left: 220px;
    bottom: 46px;
    list-style: none;
    color: var(--text-white);
    font-weight: 400;
    font-size: 12.5px;
    line-height: 1.75;
    letter-spacing: 0.02em;
    white-space: nowrap;
  }
</style>
</head>
<body>
  <main class="card-set">
    <section class="card card--front" aria-label="Card front">
      <div class="brand-mark">
        <span class="brand-mark__dot"></span>
        <span class="brand-mark__name">Gerald Fenwick</span>
      </div>
    </section>

    <section class="card card--back" aria-label="Card back">
      <h1 class="holder-name">Gerald Fenwick</h1>
      <ul class="contact-list">
        <li>0452817360 | GeraldFenwickPhotography47@mailbox.test</li>
        <li>Ins: _Gerald_fenwick | www.GeraldFenwickPhotography.test.au</li>
      </ul>
    </section>
  </main>
</body>
</html>
```